Single-sided business card for restaurant velmora with new logo made on this site

Business card options with new logo including restaurant name, address, phone number and website. This business card is single-sided only and will be presented at the hostess desk for clients to take. I would like to see options based on a cream card background, a white card background, a yellow card background and a burgundy colored background. It needs to be elegant and traditional.

Target Market(s)

local and international crowd

Industry/Entity Type

restaurant

Contact Information for Business Card

address, website and phone number

Font styles to use
Serif

Colors
EE7325
F08F49
F5BC92
FAE3D3
FDF4ED

Requirements
Must have
• new logo, address, phone number, website
Should not have
• more than three colors

```html
<!DOCTYPE html>
<html lang="es">
<head>
<meta charset="utf-8">
<title>Restaurant Velmora – Tarjeta de presentación</title>
<link href="https://fonts.googleapis.com/css2?family=EB+Garamond:wght@400;700&display=swap" rel="stylesheet">
<style>
  :root {
    --backdrop: #e4e4e4;
    --card-top: #fdf1dc;
    --card-bottom: #fde8cb;
    --ink: #3a1a1c;
    --mark-gold: #f4b942;
    --leaf-tone: #e4d4b6;
  }
  * { margin: 0; padding: 0; box-sizing: border-box; }
  html, body {
    width: 1200px;
    height: 940px;
    overflow: hidden;
    background: var(--backdrop);
  }
  .canvas {
    position: relative;
    width: 1200px;
    height: 940px;
  }
  .business-card {
    position: absolute;
    left: 172px;
    top: 225px;
    width: 856px;
    height: 490px;
    border-radius: 24px;
    overflow: hidden;
    background: linear-gradient(180deg, var(--card-top), var(--card-bottom));
    font-family: "EB Garamond", Georgia, serif;
    color: var(--ink);
  }
  .agave-decoration {
    position: absolute;
    left: 379px;
    top: 18px;
    width: 477px;
    height: 472px;
    background: radial-gradient(ellipse 70% 85% at 70% 100%, var(--leaf-tone) 0%, rgba(228, 212, 182, 0.55) 55%, rgba(228, 212, 182, 0) 100%);
  }
  .brand-square {
    position: absolute;
    left: 90px;
    top: 35px;
    width: 106px;
    height: 104px;
    background: var(--mark-gold);
  }
  .brand-name {
    position: absolute;
    left: 55px;
    top: 150px;
    width: 200px;
    font-size: 34px;
    font-weight: 400;
    letter-spacing: 6px;
    text-align: center;
    line-height: 1;
  }
  .contact {
    position: absolute;
    left: 57px;
    top: 244px;
    font-size: 21px;
    line-height: 26.5px;
  }
  .contact .venue { font-weight: 700; }
  .contact .label {
    font-weight: 700;
    margin-top: 12px;
  }
  .contact .phone {
    font-size: 27px;
    line-height: 30px;
  }
  .contact .website {
    font-weight: 700;
    letter-spacing: 0.5px;
    margin-top: 8px;
  }
</style>
</head>
<body>
<div class="canvas">
  <div class="business-card">
    <div class="agave-decoration" role="img" aria-label="Faint decorative agave plant in pale beige rising from the lower right corner"></div>

    <div class="brand-square"></div>
    <div class="brand-name">VELMORA</div>

    <div class="contact">
      <p class="venue">Restaurant Velmora</p>
      <p>Jacaranda 415</p>
      <p>Bahías de Altamar</p>
      <p>Oaxaca CP 70912</p>
      <p class="label">Reservaciones</p>
      <p class="phone">958-214-3370</p>
      <p class="website">www.velmora.com.mx</p>
    </div>
  </div>
</div>
</body>
</html>
```